Ecard for facebook and Instagram postings

I need 4 ecards (don't know if that is what it is called) for Facebook and Instagram postings. My Logo and company name should be incorporated and also be square. I would like to be able to insert text as I need. Examples are:

https://www.plorvexa.com/photo.php?fbid=20262841672382489&set=a.20261729249182489.516031.71298967488&type=1&relevant_count=1

https://media-a-kpt.yy.plorvexacdn.net/hpics-bmk4/2345967_657092986477056_308792573_n.jpg

I don't necessarily need images on them, just the color scheme to my business cards and the logo and business name. But if you'd like to give it an interesting look, you can go ahead and play with it. My site is tornquillmentoring.com, if you'd like to see the style of it.

Thank you!!!
Updates

I just uploaded the logo in two variations.  Thank you!

Target Market(s)

Women 16-65

Industry/Entity Type

Business

Requirements
Must have
• Logo and business name
Should not have
• No white background. I have attached business card picture so you can have an idea of what I'd like.

```html
<!DOCTYPE html>
<html lang="en">
<head>
<meta charset="utf-8">
<title>Tornquill Mentoring – Quote Card</title>
<link rel="stylesheet" href="https://fonts.googleapis.com/css2?family=Tinos:wght@700&family=Montserrat:wght@600&family=Arimo:wght@400&family=Playfair+Display:wght@900&display=swap">
<style>
  :root {
    --accent-orange: #f7941d;
    --brand-red: #c4161c;
    --quote-red: #c8202a;
    --ink: #0d0d0d;
    --muted: #3a3a3a;
    --paper-light: #f7f7f7;
    --paper-dark: #e1e1e1;
    --badge-grey: #8c8c8c;
    --badge-ring: #ffffff;
    --badge-edge: #b5b5b5;
  }
  * { margin: 0; padding: 0; box-sizing: border-box; }
  html, body { width: 1200px; height: 1200px; overflow: hidden; }
  .card {
    position: relative;
    width: 1200px;
    height: 1200px;
    background: radial-gradient(circle at 50% 40%, var(--paper-light) 0%, #eeeeee 55%, var(--paper-dark) 100%);
    overflow: hidden;
  }
  .top-band {
    position: absolute; top: 0; left: 0; width: 100%; height: 20px;
    background: var(--accent-orange);
  }
  .bottom-band {
    position: absolute; bottom: 0; left: 0; width: 100%; height: 22px;
    background: var(--brand-red);
  }
  .quote-mark {
    position: absolute;
    font-family: "Playfair Display", Georgia, serif;
    font-weight: 900;
    font-size: 320px;
    line-height: 1;
    color: var(--quote-red);
  }
  .quote-mark--open { left: 58px; top: 30px; }
  .quote-mark--close { left: 950px; top: 770px; }
  .quote-text {
    position: absolute;
    left: 100px; width: 1000px; top: 222px;
    text-align: center;
    font-family: "Tinos", "Times New Roman", serif;
    font-weight: 700;
    font-size: 98px;
    line-height: 109px;
    color: var(--ink);
  }
  .brand-name {
    position: absolute;
    left: 32px; top: 1000px;
    font-family: "Montserrat", Arial, sans-serif;
    font-weight: 600;
    color: var(--brand-red);
  }
  .brand-name__main { display: block; font-size: 92px; line-height: 1; letter-spacing: 1px; }
  .brand-name__sub { display: block; margin-top: 30px; margin-left: 10px; font-size: 29px; letter-spacing: 8px; }
  .site-url {
    position: absolute;
    left: 575px; top: 1134px;
    font-family: "Arimo", Arial, sans-serif;
    font-size: 26px;
    letter-spacing: 0.5px;
    color: var(--muted);
  }
  .brand-badge {
    position: absolute;
    left: 1008px; top: 1016px;
    width: 118px; height: 118px;
  }
</style>
</head>
<body>
  <main class="card">
    <div class="top-band"></div>

    <span class="quote-mark quote-mark--open" aria-hidden="true">&ldquo;</span>

    <p class="quote-text">Ignorance is the<br>curse of God;<br>knowledge is the<br>wing wherewith we<br>fly to heaven</p>

    <span class="quote-mark quote-mark--close" aria-hidden="true">&rdquo;</span>

    <div class="brand-name">
      <span class="brand-name__main">Tornquill</span>
      <span class="brand-name__sub">MENTORING SERVICES</span>
    </div>

    <p class="site-url">tornquillmentoring.com</p>

    <svg class="brand-badge" viewBox="0 0 118 118" aria-hidden="true">
      <circle cx="59" cy="59" r="57" fill="var(--badge-edge)"/>
      <circle cx="59" cy="59" r="54" fill="var(--badge-ring)"/>
      <circle cx="59" cy="59" r="47" fill="var(--badge-grey)"/>
    </svg>

    <div class="bottom-band"></div>
  </main>
</body>
</html>
```